New Corvane Logo & Responsive Website Design for Codeworks Heron

Codeworks Heron provides a white labeled, digital lending platform technology solutions to the mortgage industry via a SaaS model. Our target market is Mortgage Companies and Banks who are looking for innovative technology to assist both borrowers and loan originators with the lending process, while automating as much of he process as possible.

Codeworks Heron is our Corvane name, and our modular software offerings Include the following Products:

1) Applicant Heron: A customizable, web based, point-of-sale application for borrowers to complete a loan application, and guide them through the mortgage process.

POS Definition
"A point of sale (POS) is the client-facing software solution that allows borrowers to create a customer portal, apply for a loan online, and seamlessly submit needed documentation."

2) Ledger Heron: A Mortgage Loan Origination System

LOS Definition
"A Mortgage Loan Origination System (LOS) is a platform that takes a completed loan application and facilitates the mortgage transaction from origination to post closing. LOS systems may include document management, pricing and eligibility engines, and compliance tools to decrease risk and increase loan manufacturing quality.

3) Dwelling Heron: A brandable, home search website

The LOS and POS definitions provided above are just for your understanding of what these products are, not to be included word-for-word as website content.

We are looking for designs that are elegant, convey technical competency, simple to navigate, and set us apart from the competition.

We are not set on any particular colors at this point, so feel free to choose the best colors for your particular designs.

Please include Corvane logo, both desktop and mobile designs with a template design for the website sub pages.

Some Examples of Mortgage Technology Websites offering similar products. These are to show the typical content, not designs that we particularly like or dislike.

https://brantiq.example/
https://www.clearvantro.example/
https://www.abodefundbuddy.example/
https://www.debtquokka.example/
https://www.ternixapps.example/products/trail

Please send comments with additional questions.

Thank You For your participation.

Mortgage Companies

```html
<!DOCTYPE html>
<html lang="en">
<head>
<meta charset="utf-8">
<title>Codeworks Heron</title>
<link href="https://fonts.googleapis.com/css2?family=Audiowide&family=Poppins:wght@400;500;600&display=swap" rel="stylesheet">
<style>
:root{
  --navy:#0f2264;
  --navy-deep:#0a1744;
  --hero-top:#17143f;
  --hero-bottom:#2c2874;
  --accent:#1fa2e4;
  --accent-soft:#9fd9f0;
  --heading:#1c98d6;
  --text:#1f2433;
  --features-bg:#d8eaf2;
  --services-bg:#eef7f7;
  --white:#ffffff;
}
*{margin:0;padding:0;box-sizing:border-box}
html,body{width:1200px;height:4511px;overflow:hidden}
body{position:relative;background:var(--white);font-family:"Poppins",sans-serif;color:var(--text)}
.abs{position:absolute}
.display{font-family:"Audiowide",sans-serif;letter-spacing:1px}
.section-title{position:absolute;left:0;width:1200px;text-align:center;font-family:"Audiowide",sans-serif;color:var(--heading);font-size:32px;letter-spacing:2px}
.lead{position:absolute;left:110px;width:980px;text-align:center;font-size:14px;line-height:25px}
.btn{position:absolute;display:flex;align-items:center;justify-content:center;background:var(--accent);color:var(--white);font-family:"Audiowide",sans-serif;font-size:16px;letter-spacing:1px;border-radius:6px}
.btn-soft{background:var(--accent-soft);color:var(--heading)}

/* hero */
.hero{position:absolute;left:0;top:0;width:1200px;height:724px}
.brand{position:absolute;left:110px;top:44px;color:var(--white);font-family:"Audiowide",sans-serif;font-size:19px;letter-spacing:2px}
.nav{position:absolute;left:543px;top:46px;display:flex;gap:21px;color:var(--white);font-size:15px}
.nav .active{color:var(--accent);font-weight:600}
.hero-art{position:absolute;left:0;top:110px;width:650px;height:460px;border-radius:20px;background:radial-gradient(ellipse at 50% 45%,#5b5dff 0%,#3a2fb8 35%,rgba(40,30,120,0) 72%)}
.hero-title{position:absolute;right:114px;top:182px;text-align:right;color:var(--white);font-family:"Audiowide",sans-serif;font-size:40px;line-height:47px;letter-spacing:2px}
.hero-text{position:absolute;right:114px;top:284px;width:420px;text-align:right;color:var(--white);font-size:14.5px;line-height:25px}

/* features */
.features{position:absolute;left:0;top:1114px;width:1200px;height:729px;background:var(--features-bg)}
.feature{position:absolute;width:478px;height:208px}
.feature.card{background:var(--white);box-shadow:0 6px 20px rgba(40,90,130,.12)}
.feature .icon{position:absolute;left:31px;top:30px;width:66px;height:66px;border-radius:50%;background:var(--accent);display:flex;align-items:center;justify-content:center}
.feature h3{position:absolute;left:120px;top:36px;width:340px;font-weight:500;font-size:22px;line-height:29px}
.feature.card h3{color:var(--heading)}
.feature p{position:absolute;left:120px;top:106px;width:330px;font-size:15px;line-height:24.5px}

/* partners */
.partner{position:absolute;width:180px;height:75px;background:var(--white);border:1px solid #e1e6ea;display:flex;align-items:center;justify-content:center;gap:10px;font-weight:600;font-size:18px;color:#2a2f3a}
.partner.hover{border:1px solid var(--accent);box-shadow:0 4px 14px rgba(31,162,228,.25)}
.partner .dot{width:22px;height:22px;border-radius:50%;background:#3a3f4c}

/* services */
.services{position:absolute;left:0;top:2292px;width:1200px;height:1520px;background:var(--services-bg)}
.svc-title{position:absolute;font-family:"Audiowide",sans-serif;color:var(--heading);font-size:20px;letter-spacing:2px}
.svc-sub{position:absolute;font-family:"Audiowide",sans-serif;color:var(--heading);font-size:19px;letter-spacing:2px}
.svc-text{position:absolute;width:478px;font-size:14.5px;line-height:23.5px;text-align:justify}
.mock{position:absolute;border-radius:14px;background:linear-gradient(160deg,#ffffff 0%,#e6eef6 100%);box-shadow:0 14px 34px rgba(30,50,90,.16)}
.mock .screen{position:absolute;left:14px;top:14px;right:14px;bottom:14px;border-radius:6px;background:linear-gradient(135deg,#f5f8fc 0%,#dfe9f5 55%,#cfe0f0 100%)}

/* testimonial + footer */
.quote-text{position:absolute;left:150px;width:900px;top:3996px;text-align:center;color:var(--white);font-size:19.5px;line-height:32px}
.quote-name{position:absolute;left:0;width:1200px;top:4088px;text-align:center;color:var(--white);font-size:20px}
.quote-name .display{letter-spacing:2px}
.foot-brand{position:absolute;left:77px;top:4220px;color:var(--white);font-family:"Audiowide",sans-serif;font-size:22px;letter-spacing:2px}
.foot-head{position:absolute;top:4220px;color:var(--white);font-family:"Audiowide",sans-serif;font-size:19px;letter-spacing:2px}
.foot-list{position:absolute;top:4260px;list-style:none;color:var(--white);font-size:13.5px;line-height:25px}
.social{position:absolute;top:4267px;width:28px;height:28px;border:1.5px solid var(--white);border-radius:50%}
.contact{position:absolute;left:879px;color:var(--white);font-size:15px;line-height:27px;display:flex;gap:14px;align-items:flex-start}
.contact .ci{width:24px;height:24px;flex:none;border:1.5px solid var(--white);border-radius:50%;display:flex;align-items:center;justify-content:center;margin-top:2px}
.copy{position:absolute;left:0;top:4432px;width:1200px;height:79px;background:var(--navy-deep);color:var(--white);font-size:14px;display:flex;align-items:center;justify-content:center}
</style>
</head>
<body>

<!-- Hero -->
<header class="hero">
  <svg class="abs" width="1200" height="724" viewBox="0 0 1200 724" style="left:0;top:0">
    <defs>
      <linearGradient id="heroBg" x1="0" y1="0" x2="0.3" y2="1">
        <stop offset="0" stop-color="#17143f"/>
        <stop offset="1" stop-color="#2c2874"/>
      </linearGradient>
    </defs>
    <path d="M0 0H1200V455C1000 520 800 640 620 715C570 735 520 730 430 705C300 670 120 640 0 622Z" fill="url(#heroBg)"/>
  </svg>
  <div class="hero-art" role="img" aria-label="Isometric illustration of a glowing laptop surrounded by floating analytics dashboards and a phone"></div>
  <div class="brand">CODEWORKS HERON</div>
  <nav class="nav">
    <span class="active">Home</span><span>How It Works</span><span>FAQs</span><span>Mortgage</span><span>Blog</span><span>About</span><span>&#128100;&#xFE0E; Login</span>
  </nav>
  <h1 class="hero-title">WELCOME TO<br>CODEWORKS HERON</h1>
  <p class="hero-text">Lorem ipsum dolor sit amet, consectetur adipiscing elit, sed do eiusmod tempor incididunt ut labore et dolore magna aliqua.</p>
  <div class="btn" style="left:871px;top:376px;width:215px;height:56px">GET STARTED</div>
</header>

<!-- About -->
<h2 class="section-title" style="top:805px">ABOUT</h2>
<p class="lead" style="top:860px">Lorem ipsum dolor sit amet, consectetur adipiscing elit, sed do eiusmod tempor incididunt ut labore et dolore magna aliqua. Ut enim ad minim veniam, quis nostrud exercitation ullamco laboris nisi ut aliquip ex ea commodo consequat. Duis aute irure dolor in reprehenderit in voluptate velit esse cillum dolore eu fugiat nulla pariatur. Excepteur sint occaecat cupidatat non proident, sunt in culpa qui officia deserunt mollit anim id est laborum.</p>
<div class="btn" style="left:505px;top:976px;width:190px;height:58px">READ MORE</div>

<!-- Features -->
<section class="features">
  <h2 class="section-title" style="top:94px">FEATURES</h2>
  <p class="lead" style="top:148px">CCLorem ipsum dolor sit amet, consectetur adipiscing elit, sed do eiusmod tempor incididunt ut labore et dolore magna aliqua. Ut enim ad minim veniam, quis nostrud exercitation ullamco laboris nisi ut aliquip ex ea commodo consequat.</p>

  <div class="feature card" style="left:110px;top:238px">
    <div class="icon" style="background:var(--white);border:3px solid var(--accent)">
      <svg width="44" height="44" viewBox="0 0 44 44"><circle cx="22" cy="22" r="19" fill="none" stroke="#1fa2e4" stroke-width="3"/><circle cx="15" cy="18" r="2.5" fill="#1fa2e4"/><circle cx="29" cy="18" r="2.5" fill="#1fa2e4"/><path d="M13 26q9 9 18 0" fill="none" stroke="#1fa2e4" stroke-width="3" stroke-linecap="round"/></svg>
    </div>
    <h3>Deliver A Modern Borrower Experience</h3>
    <p>Lorem ipsum dolor sit amet, consectetur adipiscing elit, sed do eiusmod tempor incididunt dolore magna aliqua.</p>
  </div>
  <div class="feature" style="left:611px;top:238px">
    <div class="icon"><svg width="38" height="38" viewBox="0 0 38 38" fill="none" stroke="#fff" stroke-width="2.5"><path d="M6 32h26"/><path d="M9 32V24M15 32V20M21 32V15M27 32V9"/><path d="M8 20L26 6M20 6h6v6"/></svg></div>
    <h3>Increase Borrower Conversions</h3>
    <p>Lorem ipsum dolor sit amet, consectetur adipiscing elit, sed do eiusmod tempor incididunt dolore magna aliqua.</p>
  </div>
  <div class="feature" style="left:110px;top:444px">
    <div class="icon"><svg width="38" height="38" viewBox="0 0 38 38" fill="none" stroke="#fff" stroke-width="2.3"><circle cx="22" cy="13" r="9"/><path d="M22 8v10M19.5 10.5h4a2 2 0 010 4h-3a2 2 0 000 4h4"/><path d="M4 27h7l6 3h7a2 2 0 000-4h-6M24 27l8-4a2 2 0 012 3l-9 6H11"/></svg></div>
    <h3>Improve Efficiency And Decrease Costs</h3>
    <p>Lorem ipsum dolor sit amet, consectetur adipiscing elit, sed do eiusmod tempor incididunt dolore magna aliqua.</p>
  </div>
  <div class="feature" style="left:611px;top:444px">
    <div class="icon"><svg width="40" height="40" viewBox="0 0 40 40" fill="none" stroke="#fff" stroke-width="2.3"><circle cx="20" cy="20" r="13"/><circle cx="20" cy="20" r="5"/><path d="M20 3v5M20 32v5M3 20h5M32 20h5M8 8l3.5 3.5M28.5 28.5L32 32M8 32l3.5-3.5M28.5 11.5L32 8"/></svg></div>
    <h3>Future-proof Your Organization</h3>
    <p>Lorem ipsum dolor sit amet, consectetur adipiscing elit, sed do eiusmod tempor incididunt dolore magna aliqua.</p>
  </div>
</section>

<!-- Partners -->
<h2 class="section-title" style="top:1920px">PARTNERSHIP WITH:</h2>
<p class="lead" style="top:1970px">CCLorem ipsum dolor sit amet, consectetur adipiscing elit, sed do eiusmod tempor incididunt ut labore et dolore magna aliqua. Ut enim ad minim veniam, quis nostrud exercitation ullamco laboris nisi ut aliquip ex ea commodo consequat.</p>
<div class="partner" style="left:110px;top:2041px"><span class="dot"></span>Linkora</div>
<div class="partner" style="left:310px;top:2041px"><span class="dot"></span>Marquell</div>
<div class="partner" style="left:510px;top:2041px"><span class="dot"></span>Corvane</div>
<div class="partner" style="left:710px;top:2041px"><span class="dot"></span>Lumibay</div>
<div class="partner" style="left:909px;top:2041px"><span class="dot"></span>Septora</div>
<div class="partner" style="left:210px;top:2134px"><span class="dot"></span>Tekvolt</div>
<div class="partner" style="left:410px;top:2134px"><span class="dot"></span>Mindforge</div>
<div class="partner hover" style="left:610px;top:2134px;color:var(--navy)"><span class="dot" style="background:var(--accent)"></span>Nimbra</div>
<div class="partner" style="left:809px;top:2134px"><span class="dot"></span>Callivo</div>

<!-- Services -->
<section class="services">
  <h2 class="section-title" style="top:116px">OUR SERVICES</h2>
  <p class="lead" style="top:170px">Lorem ipsum dolor sit amet, consectetur adipiscing elit, sed do eiusmod tempor incididunt ut labore et dolore magna aliqua. Ut enim ad minim veniam, quis nostrud exercitation ullamco laboris nisi ut aliquip ex ea commodo consequat.</p>

  <div class="svc-title" style="left:110px;top:298px">APPLICANT HERON</div>
  <p class="svc-text" style="left:110px;top:333px">A customizable, web based, point-of-sale application for borrowers to complete a loan application, and guide them through the mortgage process.</p>
  <div class="svc-sub" style="left:110px;top:417px">POS :</div>
  <p class="svc-text" style="left:110px;top:447px;text-align:left">A point of sale (POS) is the client-facing software solution that allows borrowers to create a customer portal, apply for a loan online, and seamlessly submit needed documentation.”</p>
  <div class="btn btn-soft" style="left:110px;top:532px;width:165px;height:58px">READ MORE</div>
  <div class="mock" style="left:613px;top:266px;width:470px;height:250px" role="img" aria-label="Laptop and phone screens showing a lending analytics dashboard"><div class="screen"></div></div>

  <div class="mock" style="left:114px;top:673px;width:480px;height:270px;border-radius:14px 14px 30px 30px" role="img" aria-label="Laptop displaying a loan origination dashboard with charts"><div class="screen"></div></div>
  <div class="svc-title" style="left:613px;top:663px">LEDGER HERON</div>
  <p class="svc-text" style="left:613px;top:697px">A customizable, web based, point-of-sale application for borrowers to complete a loan application, and guide them through the mortgage process.</p>
  <div class="svc-sub" style="left:613px;top:782px">LOS :</div>
  <p class="svc-text" style="left:613px;top:812px">A Mortgage Loan Origination System (LOS) is a platform that takes a completed loan application and facilitates the mortgage transaction from origination to post closing.</p>
  <div class="btn btn-soft" style="left:613px;top:900px;width:165px;height:58px">READ MORE</div>

  <div class="svc-title" style="left:110px;top:1070px">DWELLING HERON</div>
  <p class="svc-text" style="left:110px;top:1102px;text-align:left">A brandable, home search website .<br>Lorem ipsum dolor sit amet, consectetur adipiscing elit, sed do eiusmod tempor incididunt ut labore et dolore magna aliqua. Ut enim ad minim veniam, quis nostrud exercitation ullamco laboris nisi ut aliquip ex ea commodo consequat.Lorem ipsum dolor sit amet, consectetur adipiscing elit</p>
  <div class="btn btn-soft" style="left:110px;top:1263px;width:168px;height:58px">READ MORE</div>
  <div class="mock" style="left:617px;top:1045px;width:478px;height:330px" role="img" aria-label="Laptop and phone showing a home search site with market charts"><div class="screen"></div></div>
</section>

<!-- Testimonial -->
<svg class="abs" width="1200" height="732" viewBox="0 0 1200 732" style="left:0;top:3700px">
  <path d="M0 294C250 250 700 40 1000 32C1090 30 1160 80 1200 110V732H0Z" fill="#0f2264"/>
</svg>
<svg class="abs" width="40" height="34" viewBox="0 0 40 34" style="left:592px;top:3906px"><path d="M2 2h12l-6 30H0zM24 2h12l-6 30h-8z" fill="#fff"/></svg>
<p class="quote-text">Lorem ipsum dolor sit amet, consectetur adipiscing elit, sed do eiusmod tempor incididunt ut labore et dolore magna aliqua. Ut enim ad minim veniam, quis nostrud exercitation ullamco laboris nisi ut aliquip ex ea commodo consequat.</p>
<p class="quote-name"><span class="display">MAREN TOLVIK</span> - Lorem ipsum</p>

<!-- Footer -->
<footer>
  <div class="foot-brand">CODEWORKS HERON</div>
  <span class="social" style="left:77px"></span>
  <span class="social" style="left:114px"></span>
  <span class="social" style="left:151px"></span>
  <span class="social" style="left:188px"></span>

  <div class="foot-head" style="left:415px">HOME</div>
  <ul class="foot-list" style="left:417px"><li>Home</li><li>How It Works</li><li>FAQs</li><li>Mortgage</li><li>Blog</li><li>About</li></ul>

  <div class="foot-head" style="left:594px">SERVICES</div>
  <ul class="foot-list" style="left:597px;line-height:31px;font-size:14.5px"><li>Applicant Heron</li><li>Ledger Heron</li><li>Dwelling Heron</li></ul>

  <div class="foot-head" style="left:879px">CONTACT US</div>
  <div class="contact" style="top:4256px"><span class="ci"><svg width="12" height="12" viewBox="0 0 12 12"><path d="M2 1l2 0 1 3-1.5 1a6 6 0 003 3L8 7l3 1v2c0 1-1 1-1 1A9 9 0 011 2s0-1 1-1z" fill="#fff"/></svg></span>+1 555 014 2290</div>
  <div class="contact" style="top:4310px"><span class="ci"><svg width="12" height="10" viewBox="0 0 12 10" fill="none" stroke="#fff" stroke-width="1.3"><rect x="1" y="1" width="10" height="8"/><path d="M1 1l5 4 5-4"/></svg></span>hello@codeworksheron.example</div>
  <div class="contact" style="top:4356px"><span class="ci" style="margin-top:14px"><svg width="10" height="13" viewBox="0 0 10 13"><path d="M5 0a5 5 0 015 5c0 3-5 8-5 8S0 8 0 5a5 5 0 015-5z" fill="#fff"/><circle cx="5" cy="5" r="1.8" fill="#0f2264"/></svg></span><span>Lorem ipsum dolor sit amet<br># 640.Lorem</span></div>

  <div class="copy">©Copyrights 2022 &nbsp;Codeworks Heron | All Rights Reserved</div>
</footer>

</body>
</html>
```